Digital One Pager for Consulting Practice

I would like the essence of the content in my ppt consolidated into a one-pager. The one-pager will mainly be sent via email as a pdf and intended to excite and invite new clients and establish the credibility of my boutique high-end consulting firm. Infographics and symbols would be a plus. The target client should view the firm as providing premeir service. The client is getting a thought partner.

Target Market(s)

Large Medical Device Manufacturer Executives, Early-Stage Medical Device Manufacturer Executives, Partners at VC Firms

Industry/Entity Type

Medical Equipment

Colors
0355a3
f37122

Requirements
Must have
• Please match the color scheme in ppt. Please use the existing logo. I am very open to better graphics on the process. My photo does not need to be on the digital flyer. Hyper link to the website and email is needed.
Nice to have
• Infographics

```html
<!DOCTYPE html>
<html lang="en">
<head>
<meta charset="utf-8">
<title>Halden Ventures – One Pager</title>
<link href="https://fonts.googleapis.com/css2?family=Open+Sans:wght@400;600;700&family=Tinos&display=swap" rel="stylesheet">
<style>
  :root{
    --orange:#f37122;
    --red:#ee4a2c;
    --navy:#19263a;
    --slate:#34465a;
    --grey-hex:#a6a8ab;
    --panel:#f1f1f1;
    --text:#2f3a48;
    --muted:#6b6e72;
    --white:#ffffff;
    --page:#ffffff;
  }
  *{margin:0;padding:0;box-sizing:border-box}
  html,body{width:958px;height:1200px;overflow:hidden;background:var(--page)}
  body{font-family:"Open Sans",Arial,sans-serif;color:var(--text)}
  .sheet{position:relative;width:958px;height:1200px;overflow:hidden;background:var(--white)}

  .brand{position:absolute;left:32px;top:58px;display:flex;align-items:center;gap:14px}
  .brand-mark{width:30px;height:30px;border-radius:50%;background:var(--orange)}
  .brand-name{font-weight:700;font-size:30px;letter-spacing:2px;color:var(--navy);line-height:1;white-space:nowrap}

  .value-panel{position:absolute;left:0;top:163px;width:494px;height:267px;background:var(--navy);padding:38px 0 0 32px}
  .value-title{font-family:"Tinos",serif;font-weight:400;color:var(--orange);font-size:52px;line-height:1;margin-bottom:14px}
  .value-list{list-style:none;color:var(--white);font-size:32px;line-height:45px}

  .photo{position:absolute;left:414px;top:-30px;width:580px;height:580px}

  .side-panel{position:absolute;left:508px;top:430px;width:450px;height:688px;background:var(--panel)}
  .heading{position:absolute;left:541px;font-family:"Tinos",serif;font-weight:400;color:var(--orange);font-size:25px}
  .sub{position:absolute;left:541px;font-size:16px;font-weight:600;color:var(--text)}
  .item{position:absolute;left:541px;width:390px;padding-left:29px;font-size:15.5px;line-height:21px;color:var(--muted)}
  .item::before{content:"";position:absolute;left:2px;top:3px;width:13px;height:13px;border:1.5px solid var(--muted);border-radius:50%}
  .item::after{content:"";position:absolute;left:6px;top:7.5px;width:4px;height:4px;border-top:1.5px solid var(--muted);border-right:1.5px solid var(--muted);transform:rotate(45deg)}

  .steps{position:absolute;left:541px;top:890px;display:flex;gap:0}
  .step{width:100px;text-align:center;font-size:11px;line-height:13px;color:var(--muted);text-transform:uppercase}
  .step svg{display:block;margin:0 auto 8px}

  .partners-title{position:absolute;left:541px;top:1024px;font-size:16px;font-weight:600;color:var(--text)}
  .partner{position:absolute;height:24px;background:#c9ccd0;border-radius:2px}

  .footer{position:absolute;left:0;top:1118px;width:958px;height:82px;display:flex}
  .footer-phone{width:456px;background:var(--orange);display:flex;align-items:center;padding-left:74px;gap:22px;color:var(--white);font-size:37px}
  .footer-links{flex:1;background:var(--navy);display:flex;align-items:center;justify-content:center;font-size:17px;color:var(--white);gap:10px}
  .footer-links a{color:var(--white);text-decoration:none}

  .hexes{position:absolute;left:0;top:480px}
  .hex-title{font-family:"Open Sans",Arial,sans-serif;font-size:16.5px;fill:var(--white)}
  .hex-text{font-family:"Open Sans",Arial,sans-serif;font-size:12.5px;fill:var(--white)}
</style>
</head>
<body>
<div class="sheet">

  <div class="brand">
    <span class="brand-mark"></span>
    <span class="brand-name">HALDEN VENTURES</span>
  </div>

  <section class="value-panel">
    <h1 class="value-title">VALUE</h1>
    <ul class="value-list">
      <li>Extensive Experience</li>
      <li>Efficient Process</li>
      <li>Valued Network</li>
    </ul>
  </section>

  <div class="side-panel"></div>

  <svg class="photo" viewBox="0 0 580 580" role="img" aria-label="Photo of two business professionals talking in a bright office hallway">
    <defs>
      <linearGradient id="photoFill" x1="0" y1="0" x2="1" y2="1">
        <stop offset="0" stop-color="#e6ecef"/>
        <stop offset="0.55" stop-color="#b9c3c8"/>
        <stop offset="1" stop-color="#6f757a"/>
      </linearGradient>
    </defs>
    <circle cx="290" cy="290" r="286" fill="var(--orange)"/>
    <circle cx="290" cy="290" r="280" fill="var(--white)"/>
    <circle cx="290" cy="290" r="274" fill="url(#photoFill)"/>
  </svg>

  <svg class="hexes" width="508" height="580" viewBox="0 0 508 580">
    <polygon points="98,28 224,28 287,135 224,242 98,242 35,135" fill="var(--orange)"/>
    <polygon points="98,242 224,242 287,349 224,456 98,456 35,349" fill="var(--grey-hex)"/>
    <polygon points="292,137 418,137 481,244 418,351 292,351 229,244" fill="var(--red)"/>
    <polygon points="292,351 418,351 481,458 418,565 292,565 229,458" fill="var(--slate)"/>

    <g>
      <circle cx="161" cy="57" r="33" fill="var(--white)" stroke="var(--orange)" stroke-width="2"/>
      <rect x="145" y="60" width="6" height="13" fill="var(--orange)"/>
      <rect x="155" y="54" width="6" height="19" fill="var(--orange)"/>
      <rect x="165" y="48" width="6" height="25" fill="var(--orange)"/>
      <polyline points="142,55 154,44 162,48 178,36" fill="none" stroke="var(--orange)" stroke-width="3"/>
      <polygon points="180,33 180,42 172,35" fill="var(--orange)"/>
    </g>
    <g>
      <circle cx="353" cy="162" r="33" fill="var(--white)" stroke="var(--red)" stroke-width="2"/>
      <rect x="341" y="146" width="22" height="28" fill="var(--red)"/>
      <rect x="345" y="150" width="22" height="28" fill="var(--red)" stroke="var(--white)" stroke-width="1.5"/>
      <line x1="349" y1="158" x2="363" y2="158" stroke="var(--white)" stroke-width="1.5"/>
      <line x1="349" y1="164" x2="363" y2="164" stroke="var(--white)" stroke-width="1.5"/>
      <line x1="349" y1="170" x2="359" y2="170" stroke="var(--white)" stroke-width="1.5"/>
    </g>
    <g>
      <circle cx="161" cy="263" r="33" fill="var(--white)" stroke="var(--grey-hex)" stroke-width="2"/>
      <circle cx="161" cy="255" r="7" fill="var(--grey-hex)"/>
      <path d="M149 273 q12 -14 24 0 z" fill="var(--grey-hex)"/>
      <circle cx="161" cy="263" r="19" fill="none" stroke="var(--grey-hex)" stroke-width="2"/>
      <circle cx="142" cy="263" r="3.5" fill="var(--grey-hex)"/>
      <circle cx="180" cy="263" r="3.5" fill="var(--grey-hex)"/>
      <circle cx="161" cy="282" r="3.5" fill="var(--grey-hex)"/>
    </g>
    <g>
      <circle cx="353" cy="370" r="33" fill="var(--white)" stroke="var(--slate)" stroke-width="2"/>
      <rect x="341" y="355" width="20" height="27" fill="none" stroke="var(--slate)" stroke-width="2.5"/>
      <line x1="345" y1="362" x2="356" y2="362" stroke="var(--slate)" stroke-width="2"/>
      <line x1="345" y1="368" x2="356" y2="368" stroke="var(--slate)" stroke-width="2"/>
      <line x1="345" y1="374" x2="352" y2="374" stroke="var(--slate)" stroke-width="2"/>
      <line x1="356" y1="381" x2="369" y2="362" stroke="var(--slate)" stroke-width="3.5"/>
    </g>

    <text class="hex-title" x="161" y="128" text-anchor="middle">REGULATORY</text>
    <text class="hex-title" x="161" y="151" text-anchor="middle">STRATEGY</text>
    <text class="hex-text" x="161" y="174" text-anchor="middle">RAQA Organizational Structure</text>
    <text class="hex-text" x="161" y="193" text-anchor="middle">Regulatory Pathway</text>

    <text class="hex-title" x="355" y="234" text-anchor="middle">FDA</text>
    <text class="hex-title" x="355" y="257" text-anchor="middle">COMMUNICATIONS</text>
    <text class="hex-text" x="355" y="283" text-anchor="middle">Deficiency Response</text>
    <text class="hex-text" x="355" y="302" text-anchor="middle">Application Review</text>

    <text class="hex-title" x="161" y="336" text-anchor="middle">INTERIM</text>
    <text class="hex-title" x="161" y="359" text-anchor="middle">EXECUTIVE LEADERSHIP</text>
    <text class="hex-text" x="161" y="392" text-anchor="middle">Compliance Remediation</text>
    <text class="hex-text" x="161" y="411" text-anchor="middle">Accelerated Product</text>
    <text class="hex-text" x="161" y="430" text-anchor="middle">Registration</text>

    <text class="hex-title" x="355" y="449" text-anchor="middle">TRAINING</text>
    <text class="hex-text" x="355" y="478" text-anchor="middle">FDA Communication</text>
    <text class="hex-text" x="355" y="497" text-anchor="middle">MDR Reporting</text>
  </svg>

  <h2 class="heading" style="top:556px">Experience to Provide...</h2>
  <h3 class="sub" style="top:598px">Executive Application Review</h3>
  <p class="item" style="top:625px">Examples include: Presubmission, IDE, 510(k), 513(g), PMA, Refuse to Accept, Hold letter</p>
  <p class="item" style="top:682px">Troubleshooting</p>
  <h3 class="sub" style="top:728px">Strategic Advice &amp; Diligence to Investors</h3>
  <p class="item" style="top:757px">Validate &amp; Verify Founder Milestones</p>
  <p class="item" style="top:789px">Diligence portfolio company Regulatory and Quality systems</p>

  <h2 class="heading" style="top:842px">Efficient Process</h2>
  <div class="steps">
    <div class="step">
      <svg width="66" height="66" viewBox="0 0 66 66"><circle cx="33" cy="33" r="32" fill="var(--orange)"/><circle cx="33" cy="28" r="8" fill="var(--white)"/><path d="M20 47 q13 -16 26 0 z" fill="var(--white)"/><path d="M22 30 a11 11 0 0 1 22 0" fill="none" stroke="var(--white)" stroke-width="2.5"/></svg>
      Exploratory<br>Call
    </div>
    <div class="step">
      <svg width="66" height="66" viewBox="0 0 66 66"><circle cx="33" cy="33" r="32" fill="var(--orange)"/><rect x="21" y="18" width="20" height="28" fill="none" stroke="var(--white)" stroke-width="2.5"/><line x1="25" y1="25" x2="37" y2="25" stroke="var(--white)" stroke-width="2"/><line x1="25" y1="31" x2="33" y2="31" stroke="var(--white)" stroke-width="2"/><circle cx="39" cy="39" r="6" fill="var(--orange)" stroke="var(--white)" stroke-width="2.5"/><line x1="43" y1="43" x2="48" y2="48" stroke="var(--white)" stroke-width="3"/></svg>
      Regulatory<br>Landscape
    </div>
    <div class="step">
      <svg width="66" height="66" viewBox="0 0 66 66"><circle cx="33" cy="33" r="32" fill="var(--orange)"/><circle cx="33" cy="28" r="10" fill="var(--white)"/><rect x="28" y="36" width="10" height="8" fill="var(--white)"/><rect x="29" y="46" width="8" height="3" fill="var(--white)"/></svg>
      Problem<br>Statement
    </div>
    <div class="step">
      <svg width="66" height="66" viewBox="0 0 66 66"><circle cx="33" cy="33" r="32" fill="var(--orange)"/><circle cx="28" cy="36" r="9" fill="none" stroke="var(--white)" stroke-width="4" stroke-dasharray="4 3"/><circle cx="28" cy="36" r="3" fill="var(--white)"/><circle cx="41" cy="24" r="6" fill="none" stroke="var(--white)" stroke-width="3" stroke-dasharray="3 2"/></svg>
      Review &amp; Align<br>on Deliverables
    </div>
  </div>

  <h3 class="partners-title">Valued Partner Network</h3>
  <div class="partner" style="left:541px;top:1052px;width:216px;height:18px"></div>
  <div class="partner" style="left:762px;top:1050px;width:46px"></div>
  <div class="partner" style="left:814px;top:1048px;width:62px;height:28px;background:var(--navy)"></div>
  <div class="partner" style="left:546px;top:1085px;width:46px"></div>
  <div class="partner" style="left:598px;top:1084px;width:50px;height:26px;background:#0d6fb8"></div>
  <div class="partner" style="left:654px;top:1085px;width:58px"></div>

  <footer class="footer">
    <div class="footer-phone">
      <svg width="34" height="34" viewBox="0 0 34 34" aria-hidden="true"><circle cx="17" cy="17" r="15" fill="none" stroke="var(--white)" stroke-width="2.5"/><path d="M11 9 l4 0 l1.5 4.5 l-2.5 2 q2 4 5 5 l2 -2.5 l4.5 1.5 l0 4 q-12 1 -14.5 -14.5 z" fill="var(--white)"/></svg>
      <span>555.014.2280</span>
    </div>
    <div class="footer-links">
      <a href="https://www.haldenventures.com">www.haldenventures.com</a>
      <span>|</span>
      <a href="mailto:info@haldenventures.com">info@haldenventures.com</a>
    </div>
  </footer>

</div>
</body>
</html>
```